TALMORK

The business want a professional looking business card. We have a scetch we will add but want the extra upgrade, and would like more suggestions for variations of our business cards.

```html
<!DOCTYPE html>
<html lang="en">
<head>
<meta charset="utf-8">
<title>TALMORK Business Card</title>
<link href="https://fonts.googleapis.com/css2?family=Playfair+Display:ital,wght@0,600;1,700&family=Montserrat:wght@400;500&display=swap" rel="stylesheet">
<style>
  :root {
    --backdrop: #1c1c1e;
    --card: #131313;
    --card-front: #161616;
    --gold: #c99a2e;
    --gold-light: #e2bb5a;
    --silver: #c9c9c9;
    --muted: #6e6e6e;
    --white: #f2f2f2;
  }
  * { margin: 0; padding: 0; box-sizing: border-box; }
  html, body {
    width: 1200px; height: 900px; overflow: hidden;
    background: var(--backdrop);
  }
  .sheet {
    width: 1200px; height: 900px;
    display: flex; flex-direction: column;
    align-items: center; justify-content: center; gap: 60px;
  }
  .card {
    width: 560px; height: 320px;
    border-radius: 26px;
    position: relative;
    box-shadow: 0 14px 30px rgba(0,0,0,.55);
  }
  /* Front */
  .card--front { background: var(--card-front); }
  .front-brand {
    position: absolute; left: 70px; top: 92px;
    font-family: "Playfair Display", serif; font-weight: 600;
    font-size: 82px; letter-spacing: 6px; color: var(--silver);
    line-height: 1;
  }
  .front-since {
    position: absolute; left: 76px; top: 200px;
    font-family: "Montserrat", sans-serif; font-weight: 500;
    font-size: 17px; letter-spacing: 14px; color: var(--muted);
  }
  /* Back */
  .card--back { background: var(--card); }
  .brand-block {
    position: absolute; left: 48px; top: 106px; width: 220px;
    display: flex; flex-direction: column; align-items: center;
  }
  .brand-mark {
    width: 14px; height: 14px; border-radius: 50%;
    background: var(--gold); margin-bottom: 14px;
  }
  .brand-name {
    font-family: "Playfair Display", serif; font-weight: 600;
    font-size: 38px; letter-spacing: 2px; color: var(--gold); line-height: 1;
  }
  .brand-since {
    margin-top: 10px;
    font-family: "Montserrat", sans-serif; font-size: 10px;
    letter-spacing: 6px; color: var(--gold);
  }
  .divider {
    position: absolute; left: 292px; top: 70px;
    width: 1.5px; height: 180px; background: var(--gold);
  }
  .contact-block { position: absolute; left: 318px; top: 90px; }
  .person-name {
    font-family: "Playfair Display", serif; font-style: italic; font-weight: 700;
    font-size: 24px; color: var(--gold-light); white-space: nowrap;
  }
  .person-role {
    margin-top: 4px; margin-bottom: 16px;
    font-family: "Montserrat", sans-serif; font-size: 13px; color: var(--white);
  }
  .contact-list { list-style: none; }
  .contact-item {
    display: flex; align-items: center; gap: 8px;
    font-family: "Montserrat", sans-serif; font-size: 12.5px;
    color: var(--white); margin-bottom: 7px;
  }
  .contact-icon { width: 12px; height: 12px; fill: var(--gold); flex: none; }
</style>
</head>
<body>
<main class="sheet">
  <section class="card card--front" aria-label="Card front">
    <div class="front-brand">TALMORK</div>
    <div class="front-since">SINCE 2026</div>
  </section>

  <section class="card card--back" aria-label="Card back">
    <div class="brand-block">
      <span class="brand-mark"></span>
      <span class="brand-name">TALMORK</span>
      <span class="brand-since">SINCE 2026</span>
    </div>
    <div class="divider"></div>
    <div class="contact-block">
      <div class="person-name">Lars Henrik Solberg</div>
      <div class="person-role">CEO &amp; Founder</div>
      <ul class="contact-list">
        <li class="contact-item">
          <svg class="contact-icon" viewBox="0 0 24 24"><path d="M6.6 10.8a15.1 15.1 0 0 0 6.6 6.6l2.2-2.2a1 1 0 0 1 1-.25 11.4 11.4 0 0 0 3.6.57 1 1 0 0 1 1 1V20a1 1 0 0 1-1 1A17 17 0 0 1 3 4a1 1 0 0 1 1-1h3.5a1 1 0 0 1 1 1c0 1.25.2 2.45.57 3.57a1 1 0 0 1-.25 1z"/></svg>
          004791234567
        </li>
        <li class="contact-item">
          <svg class="contact-icon" viewBox="0 0 24 24"><path d="M2 5h20v14H2z M2 5l10 8 10-8" fill="none" stroke="var(--gold)" stroke-width="2.4"/></svg>
          talmork.llc@mailhost.com
        </li>
        <li class="contact-item">
          <svg class="contact-icon" viewBox="0 0 24 24"><circle cx="12" cy="12" r="9.5" fill="none" stroke="var(--gold)" stroke-width="2.4"/><path d="M2.5 12h19M12 2.5c3 3 3 16 0 19M12 2.5c-3 3-3 16 0 19" fill="none" stroke="var(--gold)" stroke-width="1.8"/></svg>
          www.talmork.llc
        </li>
      </ul>
    </div>
  </section>
</main>
</body>
</html>
```